a business advisory consulting website

I need a website 3-5 pages to sell my professional services in IT and Project management Consulting. My company name is Crestline Advisory Consulting. I want it to be device friendly and easy to navigate for the busy executive however intriguing enough.
I have attached some info I drafted on About the company and personal Bio. Also there is a website that I really like that I have attached the initial site pdf and websites that I like are here: https://tollmeradvisors.example, https://quarvelanalytics.example, https://www.dorvikstudylearning.example as examples. Thanks
Updates

Hi Designers, I have uploaded the logo in 3D .png format, to assist in the web design.

Target Market(s)

B2B, governments, IT companies, Project Management companies and Consulting firms, small medium enterprises to large corporate enterprises.

Industry/Entity Type

It Professional

Coding

Coded - Design and coding required

Number of Pages Required

5+ page

Font styles to use
Sans Serif

Requirements
Must have
• Home, About company, the team, what we do and contact us
Nice to have
• Blog
Should not have
• pop ups, flash

```html
<!DOCTYPE html>
<html lang="en">
<head>
<meta charset="utf-8">
<title>Crestline Advisory Consulting</title>
<link rel="stylesheet" href="https://fonts.googleapis.com/css2?family=Montserrat:wght@500;600;700&family=Roboto:wght@400;500;700&display=swap">
<style>
:root{
  --navy:#1f2748;
  --navy-deep:#16203f;
  --red:#e3282d;
  --ink:#222;
  --text:#333;
  --muted:#777;
  --white:#fff;
  --footer:#1d1d1f;
  --photo-grey:#d9d7d4;
}
*{margin:0;padding:0;box-sizing:border-box}
html,body{width:1200px;height:3741px;overflow:hidden}
body{position:relative;background:var(--white);font-family:"Roboto",Arial,sans-serif;color:var(--text)}
.abs{position:absolute}
h1,h2,.heading{font-family:"Montserrat",Arial,sans-serif;font-weight:500}

/* header */
.site-header{position:absolute;top:0;left:0;width:1200px;height:97px;background:var(--white);border-top:3px solid var(--red);z-index:5}
.brand{position:absolute;display:flex;align-items:center;gap:10px}
.brand-mark{width:26px;height:26px;background:var(--red)}
.brand-name{font-family:"Montserrat",Arial,sans-serif;font-weight:700;line-height:1;text-transform:uppercase}
.site-header .brand{left:90px;top:14px}
.site-header .brand-name{color:var(--navy);font-size:25px}
.nav{position:absolute;top:40px;left:0;font-family:"Roboto",sans-serif;font-weight:700;font-size:13.5px;letter-spacing:.6px}
.nav a{position:absolute;white-space:nowrap;color:var(--ink);text-decoration:none}
.nav a.active{color:var(--red)}

/* hero */
.hero-photo{position:absolute;left:0;top:97px;width:1200px;height:637px}
.hero-title{position:absolute;left:92px;top:212px;font-size:70px;line-height:70px;color:var(--navy);font-weight:600}
.hero-sub{position:absolute;left:90px;top:370px;font-size:21px;color:var(--red)}
.btn{position:absolute;display:flex;align-items:center;justify-content:center;background:var(--navy);color:var(--white);border-radius:26px;font-weight:700;font-size:16px;text-decoration:none}
.dots span{position:absolute;width:13px;height:13px;border-radius:50%;background:var(--white);top:630px}
.dots span.on{background:var(--red)}

/* about */
.section-title{position:absolute;font-size:46px;line-height:1;color:var(--ink);font-weight:500}
.about-copy{position:absolute;left:90px;top:872px;width:516px;font-size:15px;line-height:36px;text-align:justify;color:var(--text)}

/* services */
.services{position:absolute;left:0;top:1313px;width:1200px;height:550px;background:linear-gradient(180deg,#1b2552 0%,#1a2247 60%,#15193a 100%)}
.service{position:absolute;width:340px;color:var(--white)}
.service h3{font-family:"Roboto",sans-serif;font-weight:700;font-size:17.5px;line-height:23px;text-transform:uppercase}
.service p{font-size:15.5px;line-height:27px}
.service.left{text-align:right}

/* approach */
.approach-item{position:absolute;left:555px;width:560px}
.approach-item h3{position:absolute;left:76px;top:0;font-family:"Roboto",sans-serif;font-weight:500;font-size:18px;color:var(--ink)}
.approach-item p{position:absolute;left:76px;top:26px;width:500px;font-size:15px;line-height:28px;color:var(--muted)}
.approach-item svg{position:absolute;left:0;top:4px}

/* bio */
.bio{position:absolute;left:0;top:2486px;width:1200px;height:494px;background:var(--red);overflow:hidden}
.bio-copy{position:absolute;left:89px;width:680px;font-size:15px;line-height:27px;color:var(--white)}

/* testimonials */
.avatar{position:absolute;width:137px;height:137px;border-radius:50%}
.t-name{position:absolute;font-family:"Montserrat",sans-serif;font-weight:500;font-size:19px;letter-spacing:1px;color:var(--ink)}
.t-text{position:absolute;width:312px;font-size:15.5px;line-height:27px;color:var(--muted);text-align:justify}
.arrow{position:absolute;top:3180px}

/* footer */
.site-footer{position:absolute;left:0;top:3353px;width:1200px;height:388px;background:var(--footer);color:var(--white)}
.site-footer .brand{left:90px;top:80px}
.site-footer .brand-name{color:var(--red);font-size:27px}
.f-col{position:absolute;top:94px}
.f-col h4{font-family:"Roboto",sans-serif;font-weight:700;font-size:16px;letter-spacing:.8px;margin-bottom:17px}
.f-col a{display:flex;align-items:center;gap:14px;color:var(--white);text-decoration:none;font-size:14.5px;letter-spacing:.5px;line-height:30.5px}
.f-col .dot{width:10px;height:10px;border-radius:50%;background:var(--white)}
.copyright{position:absolute;left:0;width:1200px;top:346px;text-align:center;font-size:12.5px}
</style>
</head>
<body>

<header class="site-header">
  <div class="brand">
    <span class="brand-mark"></span>
    <span class="brand-name">Crestline<br>Advisory</span>
  </div>
  <nav class="nav">
    <a class="active" style="left:481px">HOME</a>
    <a style="left:571px">ABOUT COMPANY</a>
    <a style="left:748px">THE TEAM</a>
    <a style="left:870px">WHAT WE DO</a>
    <a style="left:1013px">CONTACT US</a>
  </nav>
</header>

<!-- hero -->
<svg class="hero-photo" viewBox="0 97 1200 637" role="img" aria-label="Photo of two businesswomen reviewing work on a laptop in a bright office">
  <defs>
    <linearGradient id="heroTone" x1="0" y1="0" x2="1" y2="0">
      <stop offset="0" stop-color="#ecebea"/>
      <stop offset=".45" stop-color="#e0dcd8"/>
      <stop offset=".75" stop-color="#b9bfc9"/>
      <stop offset="1" stop-color="#8c9a7a"/>
    </linearGradient>
  </defs>
  <polygon points="0,97 1200,97 1200,636 596,734 0,636" fill="url(#heroTone)"/>
</svg>
<h1 class="hero-title">CRESTLINE<br>ADVISORY</h1>
<p class="hero-sub">Lorem ipsum dolor sit amet,consectetur ut labore</p>
<a class="btn" style="left:92px;top:437px;width:155px;height:50px">Read More</a>
<div class="dots">
  <span class="on" style="left:553px"></span>
  <span style="left:581px"></span>
  <span style="left:607px"></span>
  <span style="left:635px"></span>
</div>

<!-- about -->
<h2 class="section-title" style="left:90px;top:815px">ABOUT US</h2>
<div class="about-copy">
  <p>We are a specialist operational excellence firm, delivering consulting and advisory services in six core capabilities, across all industries and all business lines to improve performance, efficiency, profitability, automation and scalability, for clients across Australia.</p>
  <p>We're known for our pragmatism, in depth analysis, strategic insight and nurturing long-term client self-sufficiency. We approach business consulting differently, with a Genuine Client Partnership model that builds client capability and rightsized solutions for the client.</p>
</div>
<a class="btn" style="left:90px;top:1184px;width:170px;height:50px">Read More</a>
<svg class="abs" style="left:660px;top:805px" width="490" height="440" viewBox="0 0 490 440" role="img" aria-label="Photo of two smiling business professionals in suits holding a notebook">
  <rect x="95" y="5" width="300" height="300" rx="26" transform="rotate(45 245 155) translate(20 20)" fill="var(--red)"/>
  <rect x="95" y="5" width="300" height="300" rx="26" transform="rotate(45 245 155) translate(30 -5)" fill="var(--white)"/>
  <rect x="95" y="5" width="300" height="300" rx="26" transform="rotate(45 245 155) translate(0 0)" fill="#c9d3de"/>
</svg>

<!-- services -->
<section class="services">
  <h2 class="section-title" style="left:0;width:1200px;text-align:center;top:75px;color:var(--white)">SERVICES</h2>
  <svg class="abs" style="left:0;top:0" width="1200" height="550" viewBox="0 0 1200 550" fill="none">
    <g stroke="#fff" stroke-width="1.5" stroke-dasharray="2 4">
      <polyline points="375,154 450,154 522,215"/>
      <polyline points="825,154 750,154 678,215"/>
      <polyline points="375,440 450,440 522,380"/>
      <polyline points="825,440 750,440 678,380"/>
    </g>
    <rect x="495" y="190" width="210" height="210" rx="22" transform="rotate(45 600 302)" fill="var(--red)"/>
    <rect x="495" y="182" width="210" height="210" rx="22" transform="rotate(45 600 287)" fill="var(--white)"/>
  </svg>
  <div class="brand" style="left:500px;top:258px">
    <span class="brand-mark"></span>
    <span class="brand-name" style="color:var(--navy);font-size:27px">Crestline<br>Advisory</span>
  </div>
  <div class="service left" style="left:28px;top:143px">
    <h3>Strategy Analytics +<br>Business-Process Optimization</h3>
    <p style="margin-top:8px">Lorem ipsum dolor sit amet, consectetur<br>adipiscing elit, sed do eiusmod tempor<br>incididunt ut labore et dolore</p>
  </div>
  <div class="service left" style="left:28px;top:342px">
    <p>Lorem ipsum dolor sit amet, consectetur<br>adipiscing elit, sed do eiusmod tempor<br>incididunt ut labore et dolore</p>
    <h3 style="margin-top:4px">Advise for early stage<br>startups</h3>
  </div>
  <div class="service" style="left:830px;top:143px">
    <h3>Market Entry</h3>
    <p style="margin-top:8px">Lorem ipsum dolor sit amet, consectetur<br>adipiscing elit, sed do eiusmod tempor<br>incididunt ut labore et dolore</p>
  </div>
  <div class="service" style="left:830px;top:342px">
    <p>Lorem ipsum dolor sit amet, consectetur<br>adipiscing elit, sed do eiusmod tempor<br>incididunt ut labore et dolore</p>
    <h3 style="margin-top:4px">Finance + Accounting +<br>Insurance</h3>
  </div>
</section>

<!-- approach -->
<svg class="abs" style="left:50px;top:1940px" width="500" height="460" viewBox="0 0 500 460" role="img" aria-label="Illustration of a businessman facing a city skyline overlaid with hexagon business icons">
  <defs>
    <linearGradient id="cityTone" x1="0" y1="0" x2="1" y2="1">
      <stop offset="0" stop-color="#c7d6e6"/>
      <stop offset=".6" stop-color="#6f8cab"/>
      <stop offset="1" stop-color="#3b5777"/>
    </linearGradient>
  </defs>
  <rect x="83" y="-7" width="316" height="316" rx="30" transform="rotate(45 241 151) translate(22 -22)" fill="var(--navy)"/>
  <rect x="83" y="-7" width="316" height="316" rx="30" transform="rotate(45 241 151) translate(8 -10)" fill="var(--white)"/>
  <rect x="83" y="-7" width="316" height="316" rx="30" transform="rotate(45 241 151)" fill="url(#cityTone)"/>
</svg>
<h2 class="section-title" style="left:555px;top:1950px">OUR APPROACH</h2>

<div class="approach-item" style="top:2014px">
  <svg width="60" height="56" viewBox="0 0 60 56" fill="none" stroke="#333" stroke-width="2"><path d="M16 4h28v14a14 14 0 0 1-28 0z"/><path d="M16 8H6v6a10 10 0 0 0 10 10M44 8h10v6a10 10 0 0 1-10 10"/><path d="M30 32v10M20 52h20v-10H20z"/><path d="M30 10l2.5 5 5.5.8-4 3.8 1 5.4-5-2.6-5 2.6 1-5.4-4-3.8 5.5-.8z"/></svg>
  <h3>Ethics And Integrity</h3>
  <p>Lorem ipsum dolor sit amet, consectetur adipiscing elit, sed do eiusmod tempor incididunt ut labore et dolore magna aliqua.</p>
</div>
<div class="approach-item" style="top:2116px">
  <svg width="60" height="56" viewBox="0 0 60 56" fill="none" stroke="#333" stroke-width="2"><path d="M56 6L4 28l16 6 4 16 8-12 14 8z"/><path d="M20 34L56 6 24 50"/><path d="M4 46l10-8M8 54l8-6"/></svg>
  <h3>Efficiency And Effectiveness</h3>
  <p>Lorem ipsum dolor sit amet, consectetur adipiscing elit, sed do eiusmod tempor incididunt ut labore et dolore magna aliqua.</p>
</div>
<div class="approach-item" style="top:2218px">
  <svg width="60" height="56" viewBox="0 0 60 56" fill="none" stroke="#333" stroke-width="2"><path d="M2 54h56"/><rect x="6" y="40" width="8" height="14"/><rect x="20" y="32" width="8" height="22"/><rect x="34" y="24" width="8" height="30"/><rect x="48" y="16" width="8" height="38"/><path d="M4 30L44 6M36 4l8 2-2 8"/></svg>
  <h3>Grow And Scale</h3>
  <p>Lorem ipsum dolor sit amet, consectetur adipiscing elit, sed do eiusmod tempor incididunt ut labore et dolore magna aliqua.</p>
</div>
<div class="approach-item" style="top:2320px">
  <svg width="60" height="50" viewBox="0 0 60 50" fill="none" stroke="#333" stroke-width="2"><circle cx="30" cy="14" r="7"/><circle cx="12" cy="20" r="5.5"/><circle cx="48" cy="20" r="5.5"/><path d="M16 44a14 14 0 0 1 28 0zM2 44a10 10 0 0 1 14-9M58 44a10 10 0 0 0-14-9"/></svg>
  <h3>Stakeholder Relationships</h3>
  <p>Lorem ipsum dolor sit amet, consectetur adipiscing elit, sed do eiusmod tempor incididunt ut labore et dolore magna aliqua.</p>
</div>

<!-- bio -->
<section class="bio">
  <svg class="abs" style="left:0;top:0" width="1200" height="494" viewBox="0 0 1200 494" role="img" aria-label="Portrait photo of a smiling consultant in a shirt and tie">
    <defs>
      <linearGradient id="bioTone" x1="0" y1="0" x2="1" y2="0">
        <stop offset="0" stop-color="#e4e8ee"/>
        <stop offset=".6" stop-color="#c9d3df"/>
        <stop offset="1" stop-color="#aebccd"/>
      </linearGradient>
    </defs>
    <path d="M1020 0 L762 240 Q750 252 762 264 L1010 494 L945 494 L760 312 Q710 260 760 210 L955 0 Z" fill="var(--navy)"/>
    <path d="M1020 0 L1200 0 L1200 494 L1010 494 L800 300 Q778 278 800 256 Z" fill="url(#bioTone)"/>
  </svg>
  <h2 class="section-title" style="left:88px;top:78px;color:var(--white)">MARCUS WENDELL BIO</h2>
  <p class="bio-copy" style="top:144px">Marcus Wendell is an IT professional with more than 20 years of experience turning business initiatives into technology solutions. His expertise has been identifying deficiencies and developing or facilitating the best solutions for an outcome that is satisfactory to all stakeholders involved.</p>
  <p class="bio-copy" style="top:252px">Marcus improves business processes as older organizations restructure or migrate to newer technologies. He bridges the gap between the actual people in these organizations transitioning and the new technologies they seek which is a value add to any organization's success.</p>
  <a class="btn" style="left:89px;top:364px;width:170px;height:50px">Read More</a>
</section>

<!-- testimonials -->
<h2 class="section-title" style="left:0;width:1200px;text-align:center;top:3055px">TESTIMONIALS</h2>
<svg class="arrow" style="left:38px" width="12" height="18" viewBox="0 0 12 18" fill="none" stroke="#555" stroke-width="1.5"><path d="M9 3L3 9l6 6"/></svg>
<svg class="arrow" style="left:1150px" width="12" height="18" viewBox="0 0 12 18" fill="none" stroke="#555" stroke-width="1.5"><path d="M3 3l6 6-6 6"/></svg>

<div class="avatar" role="img" aria-label="Client portrait photo" style="left:90px;top:3122px;background:radial-gradient(circle,#cfc9c3,#9a9590)"></div>
<p class="t-name" style="left:243px;top:3128px">Lena Hartwell</p>
<p class="t-text" style="left:243px;top:3160px">Lorem ipsum dolor sit amet, consectetur adipiscing elit, sed do eiusmod tempor incididunt ut labore et dolore magna aliqua. Ut enim ad minim veniam, quis</p>

<div class="avatar" role="img" aria-label="Client portrait photo" style="left:639px;top:3133px;background:radial-gradient(circle,#d8dde3,#8a97a8)"></div>
<p class="t-name" style="left:793px;top:3128px">Lena Hartwell</p>
<p class="t-text" style="left:793px;top:3160px">Lorem ipsum dolor sit amet, consectetur adipiscing elit, sed do eiusmod tempor incididunt ut labore et dolore magna aliqua. Ut enim ad minim veniam, quis</p>

<!-- footer -->
<footer class="site-footer">
  <div class="brand">
    <span class="brand-mark"></span>
    <span class="brand-name">Crestline<br>Advisory</span>
  </div>
  <div class="f-col" style="left:448px">
    <h4>LINKS</h4>
    <a>Home</a><a>About Company</a><a>The Team</a><a>What We Do</a><a>Contact Us</a>
  </div>
  <div class="f-col" style="left:714px">
    <h4>OTHERS</h4>
    <a>FAQ</a><a>Privacy Policy</a><a>Terms &amp; Conditions</a>
  </div>
  <div class="f-col" style="left:1004px">
    <h4>FOLLOW US</h4>
    <a><span class="dot"></span>Friendloop</a><a><span class="dot"></span>Chirpline</a><a><span class="dot"></span>Searchnet</a><a><span class="dot"></span>Worklink</a>
  </div>
  <p class="copyright">Copyright © 2020 The Company Name. All rights reserved.</p>
</footer>

</body>
</html>
```